Corvel Capital LLC

Need Professional Business cards for New Investment Fund

Target Market(s)

High Quality investors

Industry/Entity Type

Financial

Contact Information for Business Card

Phone Number +1 555 284 6190
Name Lukas Varenko
Title Fund Manager
email lv@FundCorvel.com
Website www.FundCorvel.com

Colors

Designer to choose colors to be used in the design.

Requirements
Must have
• Must have our Logo and all of the above. Must be made so lettering and loge can be raised

```html
<!DOCTYPE html>
<html lang="en">
<head>
<meta charset="utf-8">
<title>Business Cards — Fund Manager</title>
<link href="https://fonts.googleapis.com/css2?family=Lato:wght@300;400;700;900&display=swap" rel="stylesheet">
<style>
  :root {
    --backdrop: #262728;
    --card: #0a0b0d;
    --accent: #62c04a;
    --muted: #565a55;
    --muted-dark: #4a4d49;
    --rule: #3f6e34;
  }
  * { margin: 0; padding: 0; box-sizing: border-box; }
  html, body { width: 1200px; height: 970px; overflow: hidden; }
  body {
    background: var(--backdrop);
    font-family: "Lato", Arial, sans-serif;
    position: relative;
  }
  .card {
    position: absolute;
    width: 680px;
    height: 390px;
    background: var(--card);
    border-left: 6px solid var(--accent);
    border-bottom: 6px solid var(--accent);
    box-shadow: 0 14px 30px rgba(0,0,0,0.55);
  }
  .card--front { left: 110px; top: 60px; }
  .card--back { left: 410px; top: 520px; }

  .brand {
    position: absolute;
    display: flex;
    align-items: center;
    gap: 10px;
  }
  .brand__mark {
    width: 18px;
    height: 18px;
    background: var(--accent);
    flex: none;
  }
  .brand__name {
    font-weight: 700;
    font-size: 28px;
    letter-spacing: 2px;
    color: var(--accent);
    text-transform: uppercase;
    white-space: nowrap;
  }
  .card--front .brand { left: 50px; top: 172px; }
  .card--back .brand { left: 50%; top: 50%; transform: translate(-50%, -50%); }
  .card--back .brand__name { font-size: 40px; letter-spacing: 3px; }
  .card--back .brand__mark { width: 24px; height: 24px; }

  .divider {
    position: absolute;
    left: 300px;
    top: 70px;
    width: 1px;
    height: 240px;
    background: var(--rule);
  }
  .details {
    position: absolute;
    left: 335px;
    top: 92px;
  }
  .details__name {
    font-weight: 900;
    font-size: 34px;
    color: var(--accent);
    line-height: 1.1;
    white-space: nowrap;
  }
  .details__title {
    font-weight: 400;
    font-size: 17px;
    color: var(--muted-dark);
    margin-top: 4px;
  }
  .contact {
    list-style: none;
    margin-top: 26px;
  }
  .contact__item {
    display: flex;
    align-items: center;
    gap: 12px;
    font-size: 16px;
    font-weight: 400;
    color: var(--muted);
    margin-bottom: 12px;
  }
  .contact__icon { width: 16px; height: 16px; flex: none; }
</style>
</head>
<body>
  <section class="card card--front" aria-label="Business card front">
    <div class="brand">
      <span class="brand__mark"></span>
      <span class="brand__name">Velmarra</span>
    </div>
    <div class="divider"></div>
    <div class="details">
      <h1 class="details__name">Lukas Varenko</h1>
      <p class="details__title">Fund Manager</p>
      <ul class="contact">
        <li class="contact__item">
          <svg class="contact__icon" viewBox="0 0 16 16" aria-hidden="true"><path d="M3.5 1.5l2.5 2.5-1.5 1.8c.8 1.8 2 3 3.7 3.7l1.8-1.5 2.5 2.5-1.8 2C7 12.5 3.5 9 1.5 3.3z" fill="var(--accent)"/></svg>
          <span>+1 555 284 6190</span>
        </li>
        <li class="contact__item">
          <svg class="contact__icon" viewBox="0 0 16 16" aria-hidden="true"><rect x="1" y="3" width="14" height="10" fill="var(--accent)"/><path d="M1 3l7 6 7-6" fill="none" stroke="var(--card)" stroke-width="1.4"/></svg>
          <span>lv@FundCorvel.com</span>
        </li>
        <li class="contact__item">
          <svg class="contact__icon" viewBox="0 0 16 16" aria-hidden="true"><g fill="none" stroke="var(--accent)" stroke-width="1.3"><circle cx="8" cy="8" r="6.5"/><ellipse cx="8" cy="8" rx="3" ry="6.5"/><path d="M1.5 8h13M2.5 4.8h11M2.5 11.2h11"/></g></svg>
          <span>www.FundCorvel.com</span>
        </li>
      </ul>
    </div>
  </section>

  <section class="card card--back" aria-label="Business card back">
    <div class="brand">
      <span class="brand__mark"></span>
      <span class="brand__name">Velmarra</span>
    </div>
  </section>
</body>
</html>
```